Tolvik Commercial Cleaning is lookong for a new business card design.

A fresh new design that's professional and stylish. We need a serious upgrade to our business cards. I have included pictures of our existing ones. Our clients include professional individuals and business owners. We woupdblike something professional and upbeat. Please have fun and see what you come uo with.

Target Market(s)

Property managers, business owners, facility managers and other similar professionals

Industry/Entity Type

Janitorial

Contact Information for Business Card

Name, cell, office number, email, web address

Font styles to use
Sans Serif

Colors

Designer to choose colors to be used in the design.

Requirements
Must have
• please use the green color in our logo
Nice to have
• Bar code
Should not have
• Address

```html
<!DOCTYPE html>
<html lang="en">
<head>
<meta charset="utf-8">
<title>Tolvik Commercial Cleaning – Business Card</title>
<link rel="stylesheet" href="https://fonts.googleapis.com/css2?family=Ubuntu:wght@500;700&family=Open+Sans:wght@400&display=swap">
<style>
  :root {
    --canvas: #e9e7e3;
    --card-dark: #1f1f22;
    --card-shade: #18181a;
    --brand-green: #39b75a;
    --brand-green-deep: #2f9a4b;
    --accent-blue: #3b73b9;
    --text-light: #f1f1f1;
    --ghost: #29292c;
  }
  * { box-sizing: border-box; margin: 0; padding: 0; }
  html, body {
    width: 1200px; height: 780px; overflow: hidden;
    background: var(--canvas);
  }
  .sheet {
    width: 1200px; height: 780px;
    display: flex; align-items: center; justify-content: center; gap: 50px;
  }
  .card {
    position: relative;
    width: 540px; height: 310px;
    border-radius: 22px;
    background: var(--card-dark);
    overflow: hidden;
    box-shadow: 0 14px 30px rgba(0,0,0,0.22);
  }

  /* Front */
  .brand-name {
    position: absolute; left: 40px; top: 34px;
    font-family: "Ubuntu", sans-serif; font-weight: 700;
    font-size: 44px; line-height: 1; color: var(--brand-green);
    letter-spacing: 0.5px;
  }
  .brand-line {
    position: absolute; left: 42px; top: 86px;
    font-family: "Ubuntu", sans-serif; font-weight: 500;
    font-size: 16px; color: var(--accent-blue);
  }
  .contact-list {
    position: absolute; left: 40px; bottom: 38px;
    list-style: none;
    font-family: "Open Sans", sans-serif; font-size: 14px;
    color: var(--text-light);
  }
  .contact-list li { display: flex; align-items: center; gap: 8px; line-height: 24px; }
  .contact-list svg { width: 13px; height: 13px; flex: none; }
  .holder-name {
    position: absolute; right: 40px; top: 150px;
    font-family: "Ubuntu", sans-serif; font-weight: 700; font-size: 26px;
  }
  .holder-name .first { color: var(--brand-green); }
  .holder-name .last { color: var(--accent-blue); }
  .edge-bar {
    position: absolute; right: 0; top: 138px;
    width: 16px; height: 44px; background: var(--brand-green);
  }
  .ghost-name {
    position: absolute; right: 26px; bottom: 6px;
    font-family: "Ubuntu", sans-serif; font-weight: 700;
    font-size: 96px; line-height: 1; color: var(--ghost);
  }

  /* Back */
  .card--back .green-band {
    position: absolute; left: 0; right: 0; top: 40px; height: 212px;
    background: var(--brand-green);
  }
  .card--back .band-name {
    position: absolute; left: 0; right: 0; top: 98px;
    text-align: center;
    font-family: "Ubuntu", sans-serif; font-weight: 700;
    font-size: 62px; line-height: 1; color: var(--brand-green-deep);
  }
  .card--back .band-line {
    position: absolute; left: 0; right: 0; top: 172px;
    text-align: center;
    font-family: "Ubuntu", sans-serif; font-weight: 500;
    font-size: 18px; color: var(--brand-green-deep);
  }
</style>
</head>
<body>
<main class="sheet">
  <section class="card card--front" aria-label="Business card front">
    <div class="brand-name">Tolvik</div>
    <div class="brand-line">commercial cleaning</div>

    <div class="ghost-name" aria-hidden="true">Tolvik</div>

    <ul class="contact-list">
      <li>
        <svg viewBox="0 0 16 16" aria-hidden="true"><path fill="#39b75a" d="M3.5 1.5l2.6 2.8-1.4 1.6c.8 1.9 2.3 3.4 4.4 4.4l1.6-1.4 2.8 2.6-1.6 2.2C6.9 13.4 2.6 9.1 1.3 3.1z"/></svg>
        (555) 014-2870
      </li>
      <li>
        <svg viewBox="0 0 16 16" aria-hidden="true"><rect x="1" y="3" width="14" height="10" rx="1.5" fill="#39b75a"/><path d="M1.5 4l6.5 5 6.5-5" fill="none" stroke="#1f1f22" stroke-width="1.4"/></svg>
        mara@tolvikcleaning.com
      </li>
      <li>
        <svg viewBox="0 0 16 16" aria-hidden="true"><circle cx="8" cy="8" r="6.5" fill="none" stroke="#39b75a" stroke-width="1.6"/><path d="M1.5 8h13M8 1.5c-3 3.5-3 9.5 0 13M8 1.5c3 3.5 3 9.5 0 13" fill="none" stroke="#39b75a" stroke-width="1.2"/></svg>
        www.tolvikcleaning.com
      </li>
    </ul>

    <div class="holder-name"><span class="first">Mara</span> <span class="last">Ellison</span></div>
    <div class="edge-bar"></div>
  </section>

  <section class="card card--back" aria-label="Business card back">
    <div class="green-band"></div>
    <div class="band-name">Tolvik</div>
    <div class="band-line">commercial cleaning</div>
  </section>
</main>
</body>
</html>
```